Unterstanding People Management, Compliance and the role of the Board

I have already and existing presentation but would like to have it made nicer and more appealing. I need to have the final version back no later than this COB CET Tuesday, 30 Jan24.
I would prefer to have all in green as further, two logos need to be added:

Brennwald Institute of Management and Alpine Director Academy. For reference see an other PPP.

Target Market(s)

Board members

Colors

Designer to choose colors to be used in the design.

Requirements
Must have
• Appealing and easy to understand
Nice to have
• Add the logos from Brennwald Institute of Management and Alpine Director Academy

```html
<!DOCTYPE html>
<html lang="de">
<head>
<meta charset="utf-8">
<title>People Management, Compliance und VR – Präsentation</title>
<link href="https://fonts.googleapis.com/css2?family=Josefin+Sans:wght@400;600;700&family=Arimo:wght@400;600&display=swap" rel="stylesheet">
<style>
  :root{
    --navy:#243441;
    --navy-deep:#1e2c38;
    --gold:#fbbf0f;
    --white:#ffffff;
    --paper:#f7f7f5;
    --ink:#243441;
  }
  *{box-sizing:border-box;margin:0;padding:0}
  html,body{width:837px;height:1200px;overflow:hidden;background:var(--white)}
  .board{position:relative;width:837px;height:1200px}
  .slide{position:absolute;width:384px;height:216px;background:var(--navy);overflow:hidden;
    box-shadow:0 2px 6px rgba(0,0,0,.18);font-family:"Josefin Sans",sans-serif;color:var(--white)}
  .col-a{left:29px}.col-b{left:426px}
  .row-1{top:33px}.row-2{top:263px}.row-3{top:493px}.row-4{top:723px}.row-5{top:952px}

  .footer{position:absolute;left:0;bottom:0;width:100%;height:23px;background:var(--gold);color:var(--ink);
    font-size:5.6px;display:flex;align-items:center;justify-content:space-between;padding:1px 9px 0}
  .footer .credentials{position:absolute;left:124px}
  .logo-word{position:absolute;top:8px;font-size:13px;font-weight:600;letter-spacing:.2px}
  .logo-word.left{left:10px}.logo-word.right{right:10px}

  .kicker{font-family:"Arimo",sans-serif;font-size:5px;color:var(--gold);font-weight:600}
  .rule{position:absolute;height:1px;background:var(--gold)}

  /* cover */
  .cover-kicker{position:absolute;left:9px;top:54px;font-size:5px}
  .cover-title{position:absolute;left:10px;top:62px;font-size:13.4px;line-height:19.6px;font-weight:600}
  .cover-title em{font-style:normal;color:var(--gold)}

  /* photo hexagon */
  .hex-photo{position:absolute;left:222px;top:18px;width:142px;height:172px}

  /* section divider */
  .side-paper{position:absolute;left:0;top:0;width:79px;height:193px;background:var(--paper)}
  .hex-section{position:absolute;left:8px;top:17px;width:144px;height:166px}
  .hex-number{position:absolute;left:26px;top:70px;width:110px;text-align:center;color:var(--navy);
    font-size:47px;font-weight:700;line-height:1;letter-spacing:-1px}
  .section-text{position:absolute;left:192px;top:80px}
  .section-title{font-size:14px;line-height:19.5px;font-weight:600;letter-spacing:.4px;margin-top:3px}

  /* content */
  .content-head{position:absolute;left:23px;top:19px}
  .content-title{font-size:13px;line-height:16.5px;font-weight:600;margin-top:3px}
  .bullets{position:absolute;left:23px;list-style:none;font-family:"Arimo",sans-serif;font-size:5.4px;line-height:13.6px}
  .bullets li{position:relative;padding-left:10px}
  .bullets li.wrap{line-height:13.6px}
  .bullets li::before{content:"";position:absolute;left:0;top:4.4px;width:5px;height:5px;border-radius:50%;background:var(--gold)}
  .bullets li::after{content:"";position:absolute;left:1.4px;top:5.9px;width:1.6px;height:1.6px;border-top:.8px solid var(--navy);border-right:.8px solid var(--navy);transform:rotate(45deg)}

  /* closing */
  .thanks{position:absolute;left:192px;top:22px;font-size:22px;font-weight:600;letter-spacing:.6px}
  .thanks-copy{position:absolute;left:192px;top:66px;width:156px;font-family:"Arimo",sans-serif;font-size:4.3px;line-height:9.6px}
  .contact{position:absolute;left:192px;top:113px;font-size:4.6px;line-height:12px}
  .contact .label{padding-left:8px;font-size:5px}
  .contact li{list-style:none;display:flex;align-items:center;gap:4px}
  .contact svg{width:5px;height:5px;flex:none}
  .hex-logo{position:absolute;left:26px;top:80px;width:110px;text-align:center;color:var(--navy);font-size:36px;font-weight:600}
</style>
</head>
<body>
<main class="board">

  <!-- Slide 01: cover -->
  <section class="slide col-a row-1">
    <div class="logo-word left">Logo</div>
    <p class="kicker cover-kicker">Brennwald Institute of Management – Public Corporate Governance – VR CAS</p>
    <h1 class="cover-title">Das Zusammenspiel<br>zwischen <em>People</em><br><em>Management, Compliance</em><br>und dem VR.</h1>
    <div class="rule" style="left:0;top:146px;width:103px"></div>
    <svg class="hex-photo" viewBox="0 0 160 180" role="img" aria-label="Foto: lächelnde Geschäftsfrau mit Tablet im Büro">
      <defs><linearGradient id="g1" x1="0" y1="0" x2="1" y2="1"><stop offset="0" stop-color="#b08a6a"/><stop offset=".55" stop-color="#8a5a3c"/><stop offset="1" stop-color="#c9d6e2"/></linearGradient></defs>
      <polygon points="80,0 156,44 156,136 80,180 4,136 4,44" fill="#fbbf0f"/>
      <polygon points="74,10 146,52 146,134 74,176 2,134 2,52" fill="#243441"/>
      <polygon points="74,18 139,56 139,130 74,168 9,130 9,56" fill="url(#g1)"/>
    </svg>
    <div class="footer"><span>Miriam Albrecht-Keller</span><span class="credentials">Rechtsanwältin &nbsp;|&nbsp; LL.M &nbsp;|&nbsp; certified board member</span><span>© Copyright 2024</span></div>
  </section>

  <!-- Slide 02: section 01 -->
  <section class="slide col-b row-1">
    <div class="side-paper"></div>
    <div class="logo-word right">Logo</div>
    <svg class="hex-section" viewBox="0 0 150 170" aria-hidden="true">
      <polygon points="72,0 142,40 142,128 72,168 2,128 2,40" fill="#fbbf0f"/>
      <polygon points="76,8 142,46 142,124 76,162 10,124 10,46" fill="#243441"/>
      <polygon points="76,17 134,51 134,119 76,153 18,119 18,51" fill="#ffffff"/>
    </svg>
    <div class="hex-number">01</div>
    <div class="section-text"><p class="kicker">Compliance</p><h2 class="section-title">GRUNDLAGEN UND<br>RECHTSRAHMEN</h2></div>
    <div class="rule" style="left:192px;top:133px;width:192px"></div>
    <div class="footer"><span>Page No : 02</span><span class="credentials">Rechtsanwältin &nbsp;|&nbsp; LL.M &nbsp;|&nbsp; certified board member</span><span>© Copyright 2024</span></div>
  </section>

  <!-- Slide 03 -->
  <section class="slide col-a row-2">
    <div class="logo-word right">Logo</div>
    <div class="content-head"><p class="kicker">Compliance</p><h2 class="content-title">Grundlagen<br>und Rechtsrahmen.</h2></div>
    <div class="rule" style="left:0;top:64px;width:146px"></div>
    <ul class="bullets" style="top:70px">
      <li>Obligationenrecht (OR 717 ff für VR-Pflichten)</li>
      <li>Obligationenrecht (OR 328 ff. für Fürsorgepflichten<br>des Arbeitgebers</li>
      <li>Datenschutzgesetz (DSG 4, 6 und 7)</li>
      <li>Arbeitsgesetz (ArG für Arbeitsbedingungen)</li>
      <li>Gleichstellungesetz (GlG)</li>
      <li>FINMA-Rundschreiben und Weisungen</li>
    </ul>
    <svg class="hex-photo" viewBox="0 0 160 180" role="img" aria-label="Foto: zwei Kollegen besprechen sich mit Tablet">
      <defs><linearGradient id="g2" x1="0" y1="0" x2="1" y2="1"><stop offset="0" stop-color="#c7a98a"/><stop offset=".5" stop-color="#7d8fa0"/><stop offset="1" stop-color="#5b4a3e"/></linearGradient></defs>
      <polygon points="80,0 156,44 156,136 80,180 4,136 4,44" fill="#fbbf0f"/>
      <polygon points="74,10 146,52 146,134 74,176 2,134 2,52" fill="#243441"/>
      <polygon points="74,18 139,56 139,130 74,168 9,130 9,56" fill="url(#g2)"/>
    </svg>
    <div class="footer"><span>Page No : 03</span><span class="credentials">Rechtsanwältin &nbsp;|&nbsp; LL.M &nbsp;|&nbsp; certified board member</span><span>© Copyright 2024</span></div>
  </section>

  <!-- Slide 04: section 02 -->
  <section class="slide col-b row-2">
    <div class="side-paper"></div>
    <div class="logo-word right">Logo</div>
    <svg class="hex-section" viewBox="0 0 150 170" aria-hidden="true">
      <polygon points="72,0 142,40 142,128 72,168 2,128 2,40" fill="#fbbf0f"/>
      <polygon points="76,8 142,46 142,124 76,162 10,124 10,46" fill="#243441"/>
      <polygon points="76,17 134,51 134,119 76,153 18,119 18,51" fill="#ffffff"/>
    </svg>
    <div class="hex-number">02</div>
    <div class="section-text" style="top:68px"><p class="kicker">Compliance</p><h2 class="section-title">ROLLE UND<br>VERANTWORTLICH-<br>KEIT DES VR</h2></div>
    <div class="rule" style="left:192px;top:137px;width:192px"></div>
    <div class="footer"><span>Page No : 04</span><span class="credentials">Rechtsanwältin &nbsp;|&nbsp; LL.M &nbsp;|&nbsp; certified board member</span><span>© Copyright 2024</span></div>
  </section>

  <!-- Slide 05 -->
  <section class="slide col-a row-3">
    <div class="logo-word right">Logo</div>
    <div class="content-head" style="top:20px"><p class="kicker">Compliance <span style="font-family:'Josefin Sans',sans-serif;color:#fff;font-size:7px;font-weight:600">&nbsp;Art. 716a</span></p><h2 class="content-title" style="font-size:12.6px">Der Verwaltungsrat hat folgende unübertragbare<br>und unentziehbare Aufgaben:</h2></div>
    <div class="rule" style="left:0;top:64px;width:144px"></div>
    <ul class="bullets" style="top:69px;width:350px">
      <li>die Oberleitung der Gesellschaft und die Erteilung der nötigen Weisungen;</li>
      <li>die Festlegung der Organisation;</li>
      <li>die Ausgestaltung des Rechnungswesens, der Finanzkontrolle sowie der Finanzplanung, sofern diese für die Führung der<br>Gesellschaft notwendig ist;</li>
      <li>die Ernennung und Abberufung der mit der Geschäftsführung und der Vertretung betrauten Personen;</li>
      <li>die Oberaufsicht über die mit der Geschäftsführung betrauten Personen, namentlich im Hinblick auf</li>
      <li>die Befolgung der Gesetze, Statuten, Reglemente und Weisungen;</li>
      <li>die Erstellung des Geschäftsberichtes sowie die Vorbereitung der Generalversammlung und die Ausführung ihrer Beschlüsse;</li>
    </ul>
    <div class="footer"><span>Page No : 05</span><span class="credentials">Rechtsanwältin &nbsp;|&nbsp; LL.M &nbsp;|&nbsp; certified board member</span><span>© Copyright 2024</span></div>
  </section>

  <!-- Slide 06: section 03 -->
  <section class="slide col-b row-3">
    <div class="side-paper"></div>
    <div class="logo-word right">Logo</div>
    <svg class="hex-section" viewBox="0 0 150 170" aria-hidden="true">
      <polygon points="72,0 142,40 142,128 72,168 2,128 2,40" fill="#fbbf0f"/>
      <polygon points="76,8 142,46 142,124 76,162 10,124 10,46" fill="#243441"/>
      <polygon points="76,17 134,51 134,119 76,153 18,119 18,51" fill="#ffffff"/>
    </svg>
    <div class="hex-number">03</div>
    <div class="section-text" style="top:80px"><p class="kicker">Compliance</p><h2 class="section-title">PEOPLE<br>MANAGEMENT</h2></div>
    <div class="rule" style="left:192px;top:129px;width:192px"></div>
    <div class="footer"><span>Page No : 06</span><span class="credentials">Rechtsanwältin &nbsp;|&nbsp; LL.M &nbsp;|&nbsp; certified board member</span><span>© Copyright 2024</span></div>
  </section>

  <!-- Slide 07 -->
  <section class="slide col-a row-4">
    <div class="logo-word right">Logo</div>
    <div class="content-head" style="top:42px"><p class="kicker">Compliance</p><h2 class="content-title">People<br>Management</h2></div>
    <div class="rule" style="left:0;top:87px;width:144px"></div>
    <ul class="bullets" style="top:93px">
      <li>Personalrekrutierung- und entwicklung</li>
      <li>Arbeitnehmervertretung und Mitwirkungsrechte</li>
      <li>Lohnsystem und Leisstungsbewertung</li>
      <li>Mitarbeiterbindung und –förderung</li>
      <li>Gleichbehandlung und Antidiskriminierung</li>
    </ul>
    <svg class="hex-photo" viewBox="0 0 160 180" role="img" aria-label="Foto: jubelndes Team im Büro">
      <defs><linearGradient id="g3" x1="0" y1="0" x2="1" y2="1"><stop offset="0" stop-color="#a9b6c4"/><stop offset=".5" stop-color="#d9cfc7"/><stop offset="1" stop-color="#3f3a44"/></linearGradient></defs>
      <polygon points="80,0 156,44 156,136 80,180 4,136 4,44" fill="#fbbf0f"/>
      <polygon points="74,10 146,52 146,134 74,176 2,134 2,52" fill="#243441"/>
      <polygon points="74,18 139,56 139,130 74,168 9,130 9,56" fill="url(#g3)"/>
    </svg>
    <div class="footer"><span>Page No : 07</span><span class="credentials">Rechtsanwältin &nbsp;|&nbsp; LL.M &nbsp;|&nbsp; certified board member</span><span>© Copyright 2024</span></div>
  </section>

  <!-- Slide 08: section 04 -->
  <section class="slide col-b row-4">
    <div class="side-paper"></div>
    <div class="logo-word right">Logo</div>
    <svg class="hex-section" viewBox="0 0 150 170" aria-hidden="true">
      <polygon points="72,0 142,40 142,128 72,168 2,128 2,40" fill="#fbbf0f"/>
      <polygon points="76,8 142,46 142,124 76,162 10,124 10,46" fill="#243441"/>
      <polygon points="76,17 134,51 134,119 76,153 18,119 18,51" fill="#ffffff"/>
    </svg>
    <div class="hex-number">04</div>
    <div class="section-text" style="top:80px"><p class="kicker">Compliance</p><h2 class="section-title">COMPLIANCE<br>MANGEMENT</h2></div>
    <div class="rule" style="left:192px;top:129px;width:192px"></div>
    <div class="footer"><span>Page No : 08</span><span class="credentials">Rechtsanwältin &nbsp;|&nbsp; LL.M &nbsp;|&nbsp; certified board member</span><span>© Copyright 2024</span></div>
  </section>

  <!-- Slide 09 -->
  <section class="slide col-a row-5">
    <div class="logo-word right">Logo</div>
    <div class="content-head" style="top:46px"><p class="kicker">Compliance</p><h2 class="content-title">Compliance<br>Management</h2></div>
    <div class="rule" style="left:0;top:91px;width:144px"></div>
    <ul class="bullets" style="top:97px">
      <li>Compliance-Kultur in der Unternehmung</li>
      <li>Risikomanagement und Compliance Strategien</li>
      <li>Interne Kontrollsysteme (IKS)</li>
      <li>Schulung und Sensibilisierung</li>
    </ul>
    <svg class="hex-photo" viewBox="0 0 160 180" role="img" aria-label="Foto: Präsentation in einem Besprechungsraum">
      <defs><linearGradient id="g4" x1="0" y1="0" x2="1" y2="1"><stop offset="0" stop-color="#cfd6dd"/><stop offset=".5" stop-color="#9fb0a0"/><stop offset="1" stop-color="#e6e2dc"/></linearGradient></defs>
      <polygon points="80,0 156,44 156,136 80,180 4,136 4,44" fill="#fbbf0f"/>
      <polygon points="74,10 146,52 146,134 74,176 2,134 2,52" fill="#243441"/>
      <polygon points="74,18 139,56 139,130 74,168 9,130 9,56" fill="url(#g4)"/>
    </svg>
    <div class="footer"><span>Page No : 09</span><span class="credentials">Rechtsanwältin &nbsp;|&nbsp; LL.M &nbsp;|&nbsp; certified board member</span><span>© Copyright 2024</span></div>
  </section>

  <!-- Slide 10: closing -->
  <section class="slide col-b row-5">
    <div class="side-paper"></div>
    <svg class="hex-section" viewBox="0 0 150 170" aria-hidden="true">
      <polygon points="72,0 142,40 142,128 72,168 2,128 2,40" fill="#fbbf0f"/>
      <polygon points="76,8 142,46 142,124 76,162 10,124 10,46" fill="#243441"/>
      <polygon points="76,17 134,51 134,119 76,153 18,119 18,51" fill="#ffffff"/>
    </svg>
    <div class="hex-logo">Logo</div>
    <h2 class="thanks">THANK YOU</h2>
    <div class="rule" style="left:192px;top:53px;width:192px"></div>
    <p class="thanks-copy">Lorem ipsum dolor sit amet, consectetur adipiscing elit, sed do eius-mod tempor incididunt ut labore et dolore magna aliqua. Ut enim ad minim veniam, quis nostrud exercitation ullamco laboris nisi ut aliquip ex ea commodo consequat.</p>
    <ul class="contact">
      <li class="label">ADDRESS</li>
      <li><svg viewBox="0 0 10 10"><path d="M5 0a3.5 3.5 0 0 0-3.5 3.5C1.5 6 5 10 5 10s3.5-4 3.5-6.5A3.5 3.5 0 0 0 5 0zm0 5a1.5 1.5 0 1 1 0-3 1.5 1.5 0 0 1 0 3z" fill="#fbbf0f"/></svg>123 strret name, city name, USA</li>
      <li><svg viewBox="0 0 10 10"><path d="M2 0l2 2.5-1 1.5a6 6 0 0 0 3 3l1.5-1L10 8l-1.5 2C4 10 0 6 0 1.5z" fill="#fbbf0f"/></svg>Phone: 123 456 7890</li>
      <li><svg viewBox="0 0 10 10"><rect x="0" y="1.5" width="10" height="7" rx="1" fill="#fbbf0f"/><path d="M0.5 2l4.5 3.5L9.5 2" stroke="#243441" stroke-width="1" fill="none"/></svg>Email Address: info@companyname.example</li>
      <li><svg viewBox="0 0 10 10"><circle cx="5" cy="5" r="5" fill="#fbbf0f"/><path d="M0 5h10M5 0c-2 3-2 7 0 10M5 0c2 3 2 7 0 10" stroke="#243441" stroke-width=".8" fill="none"/></svg>Website : www.companyname.com</li>
    </ul>
    <div class="footer"><span>Page No : 10</span><span class="credentials">Rechtsanwältin &nbsp;|&nbsp; LL.M &nbsp;|&nbsp; certified board member</span><span>© Copyright 2024</span></div>
  </section>

</main>
</body>
</html>
```